Bram Keystone Homes needs a business card

We need a business card for a new company in Canada, Ontario. Our company is all about luxury contraction homes for our clients. Our product and services are custom projects design. Under the business logo that will be created, we want a slogan that will be a memorable phrase for consumers to remember us to tell their friends and relatives.

Additional infomation
- Ludovic Entrasse
- President / Ceo
-519.604.3087

Find point what luxury construction products and services can be done

We like to see colors:
- #663300
- and something other colors or color that would attract the client needs and wants

The final design should communicate leads from new or old clients that will grow our empire. Most of all, we try to work among the budget that clients want

NOTE
- we also need an icon for the business (Example: Instagram, Facebook, and Whatsapp icons)
- We want the company name to be remembered easily for clients and our distributors who would get our orders.
- we need an icon on the business cards: Facebook and Instagram.

Thanks,
Bram Keystone Homes

```html
<!DOCTYPE html>
<html lang="en">
<head>
<meta charset="utf-8">
<title>Bram Keystone Homes – Business Card</title>
<link rel="stylesheet" href="https://fonts.googleapis.com/css2?family=Work+Sans:wght@400;500;800&family=Roboto+Condensed:wght@500&display=swap">
<style>
  :root {
    --stage: #1f1f1f;
    --card-brown: #663300;
    --card-brown-light: #74441f;
    --card-brown-deep: #5e3013;
    --ink-light: #ffffff;
    --ink-emboss: #8a6247;
    --rule: #f3e9df;
  }
  * { box-sizing: border-box; margin: 0; padding: 0; }
  html, body {
    width: 1200px; height: 900px; overflow: hidden;
    background: var(--stage);
  }
  .stage {
    width: 1200px; height: 900px;
    display: flex; flex-direction: column; align-items: center; justify-content: center;
    gap: 40px;
  }
  .card {
    width: 700px; height: 400px;
    background: linear-gradient(135deg, var(--card-brown-deep) 0%, var(--card-brown) 55%, var(--card-brown-light) 100%);
    position: relative;
    color: var(--ink-light);
    font-family: "Work Sans", sans-serif;
  }
  .brand { display: flex; flex-direction: column; align-items: center; }
  .brand-name {
    font-family: "Work Sans", sans-serif;
    font-weight: 800;
    letter-spacing: -0.5px;
    line-height: 1;
    white-space: nowrap;
  }
  .brand-tagline {
    font-family: "Roboto Condensed", sans-serif;
    font-weight: 500;
    text-transform: uppercase;
    white-space: nowrap;
    margin-top: 6px;
  }
  /* front */
  .card-front { display: flex; align-items: center; justify-content: center; }
  .card-front .brand-name { font-size: 46px; color: var(--ink-emboss); }
  .card-front .brand-tagline { font-size: 17px; color: var(--ink-emboss); letter-spacing: 0.3px; }
  /* back */
  .card-back { display: flex; align-items: center; padding: 0 40px 0 44px; }
  .card-back .brand { width: 340px; }
  .card-back .brand-name { font-size: 34px; color: var(--ink-light); }
  .card-back .brand-tagline { font-size: 13px; color: var(--ink-light); }
  .divider { width: 2px; height: 190px; background: var(--rule); margin: 0 30px 0 22px; }
  .contact { display: flex; flex-direction: column; }
  .contact-name { font-size: 24px; font-weight: 500; }
  .contact-role { font-size: 19px; font-weight: 400; margin-bottom: 14px; }
  .contact-address { font-size: 17px; line-height: 1.35; margin-bottom: 12px; letter-spacing: 0.5px; }
  .contact-line { display: flex; align-items: center; gap: 10px; font-size: 17px; line-height: 1.5; letter-spacing: 0.5px; }
  .contact-line svg { width: 13px; height: 13px; flex: none; }
</style>
</head>
<body>
<main class="stage">
  <section class="card card-front" aria-label="Card front">
    <div class="brand">
      <div class="brand-name">Bram Keystone Homes</div>
      <div class="brand-tagline">- Home Renovations - Custom Project Design -</div>
    </div>
  </section>

  <section class="card card-back" aria-label="Card back">
    <div class="brand">
      <div class="brand-name">Bram Keystone Homes</div>
      <div class="brand-tagline">- Home Renovations - Custom Project Design -</div>
    </div>
    <div class="divider"></div>
    <div class="contact">
      <div class="contact-name">Ludovic Entrasse</div>
      <div class="contact-role">President / Ceo</div>
      <div class="contact-address">1875 Harrow Lane<br>Milton, ON L9T 4K2</div>
      <div class="contact-line">
        <svg viewBox="0 0 16 16" fill="none" stroke="#fff" stroke-width="1.6" aria-hidden="true"><path d="M4 1.5l2.5 3-1.6 1.6c.8 2 2.4 3.6 4.4 4.4l1.6-1.6 3 2.5-1.7 2.1C6.8 13.2 2.8 9.2 1.9 3.2z"/></svg>
        <span>519.604.3087</span>
      </div>
      <div class="contact-line">
        <svg viewBox="0 0 16 16" fill="none" stroke="#fff" stroke-width="1.6" aria-hidden="true"><rect x="1.5" y="3.5" width="13" height="9"/><path d="M1.5 3.5L8 9l6.5-5.5"/></svg>
        <span>info@bramkeystone.com</span>
      </div>
      <div class="contact-line">
        <svg viewBox="0 0 16 16" fill="none" stroke="#fff" stroke-width="1.3" aria-hidden="true"><circle cx="8" cy="8" r="6.5"/><ellipse cx="8" cy="8" rx="3" ry="6.5"/><path d="M1.5 8h13M2.5 4.8h11M2.5 11.2h11"/></svg>
        <span>www.bramkeystone.com</span>
      </div>
    </div>
  </section>
</main>
</body>
</html>
```